Website for Torvel Capital - investment banking firm

We have a corporate identity (thanks to Ravinka/31842) and want to extend that into a website design.  See the attached zipped files.
We have software folks in-house to do the coding.
See the attached Project Brief & Notes for more details.  Don't worry about the actual text - lorem ipsum will be fine.
The server will be Apache.
Thank you!
Desmond

Industry/Entity Type
Investment

```html
<!DOCTYPE html>
<html lang="en">
<head>
<meta charset="utf-8">
<title>Torvel Capital — Investment Banking</title>
<link href="https://fonts.googleapis.com/css2?family=Open+Sans:ital,wght@0,400;0,600;1,400;1,600&display=swap" rel="stylesheet">
<style>
:root{
  --brand:#1f4f9c;
  --footer:#2452a0;
  --footer-base:#1d4795;
  --text:#8a8a8a;
  --line:#e6e6e6;
  --band:#eeeeee;
  --client:#a9a9a9;
}
*{margin:0;padding:0;box-sizing:border-box}
html,body{width:706px;height:1200px;overflow:hidden;background:#fff}
body{position:relative;font-family:"Open Sans",Arial,sans-serif;color:var(--text)}
h1,h2,h3,h4{font-weight:400}
.abs{position:absolute}

/* header */
.search{left:552px;top:10px;width:110px;height:17px;border:1px solid #d8d8d8;background:#f4f4f4;border-radius:2px;font-size:7px;font-style:italic;color:#aaa;padding:3px 7px}
.search svg{position:absolute;right:4px;top:3px}
.logo{left:43px;top:31px;display:flex;align-items:center;gap:7px}
.logo-square{width:22px;height:22px;background:var(--brand)}
.logo-name{font-size:17px;color:var(--brand);letter-spacing:.3px}
.nav{right:44px;top:45px;display:flex;font-size:7.4px;color:#555;letter-spacing:.2px}
.nav span{padding:0 6px;border-left:1px solid #999;line-height:8px}
.nav span:first-child{border-left:none}
.nav span:last-child{padding-right:0}
.nav .active{color:var(--brand)}

/* hero */
.hero{left:43px;top:64px;width:619px;height:239px;border:3px solid #dedede;background:linear-gradient(90deg,#f1f4ec 0%,#e5ecd9 35%,#d8dcd6 60%,#c9cbcd 100%);overflow:hidden}
.hero-photo{position:absolute;right:0;top:0;width:330px;height:100%;background:linear-gradient(180deg,#c8cdd0 0%,#585b62 55%,#2b2d33 100%)}
.hero h1{position:absolute;left:18px;top:50px;font-size:19px;line-height:22px;font-weight:600;color:var(--brand)}
.hero h1 .or{color:#333}
.hero p{position:absolute;left:18px;top:99px;width:270px;font-size:9.6px;line-height:13px;color:#111}
.btn{background:var(--brand);color:#fff;display:flex;align-items:center;justify-content:center;border-radius:2px}
.hero .btn{position:absolute;left:15px;top:132px;width:84px;height:26px;font-size:9.6px;font-weight:600}
.dots{position:absolute;left:16px;top:213px;display:flex;gap:4px}
.dots i{width:10px;height:10px;border-radius:50%;background:#666;display:block}
.dots i.on{background:var(--brand)}

/* sections */
.section-title{left:0;width:706px;text-align:center;font-size:12.8px;color:var(--brand);letter-spacing:.2px}
.lead{left:62px;width:582px;text-align:center;font-size:7.3px;line-height:12.4px}
.divider{left:43px;width:619px;height:1px;background:linear-gradient(90deg,transparent,var(--line) 20%,var(--line) 80%,transparent)}
.small-btn{width:63px;height:21px;font-size:7.6px}
.map{left:148px;top:520px;width:432px;height:196px;background:radial-gradient(ellipse at 60% 45%,#dadada 0%,#e6e6e6 55%,#fff 80%)}

/* columns */
.col-title{top:744px;font-size:12.8px;color:var(--brand)}
.photo{top:768px;width:184px;height:83px}
.photo.meeting{background:linear-gradient(135deg,#3c4d66,#9aa7b6 60%,#d8dde2)}
.photo.strategy{background:linear-gradient(135deg,#7d7f82,#c9c9c9 55%,#2c2c2c)}
.col-text{top:862px;width:184px;font-size:7.3px;line-height:12.4px}
.col-btn{top:942px}
.testimonial{left:467px;width:195px}
.avatar{position:absolute;left:0;top:0;width:43px;height:43px;background:linear-gradient(180deg,#d9cfc4,#8a7a6c)}
.quote{position:absolute;left:53px;top:0;width:142px;font-size:7.2px;line-height:12.4px;font-style:italic}
.quote svg{vertical-align:-1px;margin-right:4px}
.author{position:absolute;right:0;font-size:7.2px;font-style:italic;font-weight:600;color:var(--brand)}
.t-rule{left:467px;top:848px;width:195px;height:1px;background:var(--line)}

/* clients */
.clients{left:0;top:981px;width:706px;height:63px;background:var(--band)}
.clients-label{left:43px;top:23px;font-size:12.8px;color:var(--brand)}
.client{top:20px;font-size:16px;font-weight:600;color:var(--client);white-space:nowrap}

/* footer */
.footer{left:0;top:1044px;width:706px;height:120px;background:var(--footer)}
.f-col{top:17px;color:#fff}
.f-col h4{font-size:9.8px;font-weight:600;margin-bottom:4px}
.f-col li{list-style:none;font-size:6.4px;line-height:14.6px}
.base{left:0;top:1164px;width:706px;height:36px;background:var(--footer-base);color:#fff}
.base-logo{left:43px;top:11px;display:flex;align-items:center;gap:5px;font-size:10px}
.base-logo i{width:13px;height:13px;background:#fff;display:block}
.copyright{right:44px;top:13px;font-size:6.4px}
</style>
</head>
<body>

<header>
  <div class="abs search">Search...
    <svg width="10" height="10" viewBox="0 0 10 10"><circle cx="4" cy="4" r="3" fill="none" stroke="#2452a0" stroke-width="1.4"/><line x1="6.2" y1="6.2" x2="9.3" y2="9.3" stroke="#2452a0" stroke-width="1.8"/></svg>
  </div>
  <div class="abs logo"><span class="logo-square"></span><span class="logo-name">Torvel Capital</span></div>
  <nav class="abs nav">
    <span class="active">HOME</span><span>ABOUT</span><span>SERVICES</span><span>CURRENT ENGAGEMENTS</span><span>COMPLETED TRANSACTIONS</span>
  </nav>
</header>

<section class="abs hero">
  <div class="hero-photo" role="img" aria-label="Photo of a team of business professionals in suits"></div>
  <h1>Global, Professional, Trusted...<br><span class="or">or</span> Disciplined / Effective?</h1>
  <p>Torvel Capital is an independent investment bank working for buyers in a number of industries.</p>
  <div class="btn">READ MORE</div>
  <div class="dots"><i class="on"></i><i></i><i></i><i></i></div>
</section>

<h2 class="abs section-title" style="top:316px">WELCOME TO TORVEL CAPITAL</h2>
<p class="abs lead" style="top:342px">Aliquam molestie, mi et imperdiet euismod, dui purus auctor tellus, et interdum lacus lectus et ante. Sed accumsan sollicitudin sapien, sit amet adipiscing turpis gravida ac. In congue, neque ac lobortis volutpat, libero mauris varius mi, vitae suscipit ipsum ligula vitae risus. Duis aliquam nibh a dui iaculis viverra id a velit. Vivamus egestas risus in magna varius commodo. Sed semper viverra egestas. Etiam pretium porttitor lectus, vel ornare neque porta volutpat.</p>
<div class="abs btn small-btn" style="left:322px;top:395px">Read More</div>
<div class="abs divider" style="top:432px"></div>

<h2 class="abs section-title" style="top:451px">GLOBAL INVESTMENT BANKING SERVICES</h2>
<p class="abs lead" style="top:476px">Aliquam molestie, mi et imperdiet euismod, dui purus auctor tellus, et interdum lacus lectus et ante. Sed accumsan sollicitudin sapien, sit amet adipiscing turpis gravida ac. In congue, neque ac lobortis volutpat, libero mauris varius mi, vitae suscipit ipsum ligula vitae risus.</p>
<div class="abs map" role="img" aria-label="World map with East Asia, Southeast Asia and Australia highlighted in green"></div>
<div class="abs divider" style="top:724px"></div>

<h3 class="abs col-title" style="left:43px">WHO WE ARE</h3>
<div class="abs photo meeting" style="left:43px" role="img" aria-label="Photo of colleagues in a business meeting"></div>
<p class="abs col-text" style="left:43px">Aliquam molestie, mi et imperdiet euismod, dui purus auctor tellus, et interdum lacus lectus et ante. Sed accumsan sollicitudin sapien, sit amet adipiscing turpis gravida ac. In congue, neque ac lobortis volutpat, libero mauris varius mi..</p>
<div class="abs btn small-btn col-btn" style="left:43px">Read More</div>

<h3 class="abs col-title" style="left:261px">WHAT WE DO</h3>
<div class="abs photo strategy" style="left:261px" role="img" aria-label="Photo of a hand moving a chess piece"></div>
<p class="abs col-text" style="left:261px">Aliquam molestie, mi et imperdiet euismod, dui purus auctor tellus, et interdum lacus lectus et ante. Sed accumsan sollicitudin sapien, sit amet adipiscing turpis gravida ac. In congue, neque ac lobortis volutpat, libero mauris varius mi..</p>
<div class="abs btn small-btn col-btn" style="left:261px">Read More</div>

<h3 class="abs col-title" style="left:467px">TESTIMONIALS</h3>
<div class="abs testimonial" style="top:768px;height:76px">
  <div class="avatar" role="img" aria-label="Portrait of a client"></div>
  <p class="quote"><svg width="11" height="8" viewBox="0 0 11 8"><path d="M0 8V4.5C0 2 1.3.5 4 0v1.6C2.7 2 2.2 2.8 2.2 4H4v4zM6 8V4.5C6 2 7.3.5 10 0v1.6C8.7 2 8.2 2.8 8.2 4H10v4z" fill="#1f4f9c"/></svg>Aliquam molestie, mi et imperdiet euismod, dui purus auctor tellus, et inter-dum lacus lectus et ante. Sed accumsan sollicitudin sapien, sit amet adipiscing turpis gravida ac...</p>
  <span class="author" style="top:64px">-Arlen Fosk</span>
</div>
<div class="abs t-rule"></div>
<div class="abs testimonial" style="top:859px;height:76px">
  <div class="avatar" role="img" aria-label="Portrait of a client"></div>
  <p class="quote"><svg width="11" height="8" viewBox="0 0 11 8"><path d="M0 8V4.5C0 2 1.3.5 4 0v1.6C2.7 2 2.2 2.8 2.2 4H4v4zM6 8V4.5C6 2 7.3.5 10 0v1.6C8.7 2 8.2 2.8 8.2 4H10v4z" fill="#1f4f9c"/></svg>Aliquam molestie, mi et imperdiet euismod, dui purus auctor tellus, et inter-dum lacus lectus et ante. Sed accumsan sollicitudin sapien, sit amet adipiscing turpis gravida ac...</p>
  <span class="author" style="top:63px">-Miren</span>
</div>
<div class="abs btn small-btn col-btn" style="left:467px">Read More</div>

<section class="abs clients">
  <h3 class="abs clients-label">OUR CLIENTS:</h3>
  <span class="abs client" style="left:150px">Bremlo</span>
  <span class="abs client" style="left:262px">Quintar</span>
  <span class="abs client" style="left:378px">Pravenco</span>
  <span class="abs client" style="left:510px">Holm &amp; Varr</span>
</section>

<footer class="abs footer">
  <div class="abs f-col" style="left:43px"><h4>Company</h4><ul><li>Ut et scelerisque ante</li><li>Donec erat purus</li><li>Faucibus vitae congu</li><li>Vel porttitor nec lectus</li><li>Suspendisse lobortis</li></ul></div>
  <div class="abs f-col" style="left:171px"><h4>Services</h4><ul><li>Ut et scelerisque ante</li><li>Donec erat purus</li><li>Faucibus vitae congu</li><li>Vel porttitor nec lectus</li><li>Suspendisse lobortis</li></ul></div>
  <div class="abs f-col" style="left:307px"><h4>Features</h4><ul><li>Ut et scelerisque ante</li><li>Donec erat purus</li><li>Faucibus vitae congu</li><li>Vel porttitor nec lectus</li><li>Suspendisse lobortis</li></ul></div>
  <div class="abs f-col" style="left:426px"><h4>Recent Posts</h4><ul><li>Ut et scelerisque ante</li><li>Donec erat purus</li><li>Faucibus vitae congu</li><li>Vel porttitor nec lectus</li><li>Suspendisse lobortis</li></ul></div>
</footer>
<div class="abs base">
  <div class="abs base-logo"><i></i>Torvel Capital</div>
  <div class="abs copyright">Copyright © 2014. All RightReserved</div>
</div>

</body>
</html>
```